The design should look similar to the uploaded example to accommodate the information needed for a business card template. I would like to see the colors orange and charcoal grey incorporated along with the logo.The following should be on the back of the card SPECIALIZING IN NEW AND USED TIRES & WHEELS FOR:- Loaders- Skid Steers- Telehandlers- Boom Lifts- Forklifs and moreELIMINATING DOWNTIMEWheel Exchange Program for New & Used Foam Filled and Solid Rubber TiresSPECIALTY SERVICES- Foam Filling Tires- Largest Tire Press in SE- ONSITE Forklift Tire Press- Boom Truck Services - Rubber Tracks

Target Market(s)

New and Existing Customers

Industry/Entity Type

Business

Contact Information for Business Card

NAMEHEAVY DUTY TIRE, LLC8470 Belvedere RoadWest Palm Beach, FL 33411P: 844-HD-TIRESF: 561-431-6469C:E: W: WWW.GRANITERIMSUPPLY-EXAMPLE.COM

Font styles to use
Sans Serif

Colors
f37122
333333

Requirements
Must have
• The logo and the information indicated for the backside of the card
Nice to have
• Keep the orange and charcoal grey colors

```html
<!DOCTYPE html>
<html lang="en">
<head>
<meta charset="utf-8">
<title>Granite Rim Supply – Business Card</title>
<link href="https://fonts.googleapis.com/css2?family=Source+Sans+3:wght@400;600;700&display=swap" rel="stylesheet">
<style>
  :root {
    --orange: #f37122;
    --orange-soft: #f6883a;
    --charcoal: #333333;
    --card: #f8f8f8;
    --page: #e6e6e6;
    --white: #ffffff;
  }
  * { margin: 0; padding: 0; box-sizing: border-box; }
  html, body { width: 1200px; height: 900px; overflow: hidden; }
  body {
    background: var(--page);
    font-family: "Source Sans 3", Arial, sans-serif;
    color: var(--charcoal);
    position: relative;
  }
  .card {
    position: absolute;
    left: 160px; top: 180px;
    width: 880px; height: 540px;
    background: var(--card);
    border-radius: 20px;
    overflow: hidden;
    box-shadow: 0 6px 24px rgba(0,0,0,0.12);
  }
  .card-name {
    position: absolute; top: 32px; left: 0; right: 0;
    text-align: center;
    color: var(--orange);
    font-weight: 600;
    font-size: 33px;
    letter-spacing: 0.5px;
  }
  .brand {
    position: absolute; top: 160px; left: 0; right: 0;
    display: flex; align-items: center; justify-content: center; gap: 16px;
  }
  .brand-dot {
    width: 54px; height: 54px; border-radius: 50%;
    background: var(--charcoal);
  }
  .brand-name {
    font-weight: 700; font-size: 42px; color: var(--charcoal);
    letter-spacing: 1px;
  }
  .contact {
    position: absolute;
    font-size: 23px;
    display: flex; align-items: center; gap: 12px;
    color: #222;
  }
  .contact svg { width: 18px; height: 18px; fill: var(--orange); flex: none; }
  .contact--left { right: 508px; }
  .contact--right { left: 483px; }
  .row-1 { top: 312px; }
  .row-2 { top: 350px; }
  .website {
    position: absolute; top: 386px; left: 0; right: 0;
    text-align: center; font-size: 23px; color: #222;
  }
  .band {
    position: absolute; left: 0; right: 0; bottom: 0; height: 100px;
    background: var(--orange-soft);
    color: var(--white);
    text-align: center;
    padding-top: 14px;
  }
  .band-company { font-weight: 700; font-size: 27px; line-height: 1.15; }
  .band-address { font-size: 23px; line-height: 1.25; }
</style>
</head>
<body>
  <div class="card">
    <div class="card-name">MARCUS DALTON</div>

    <div class="brand">
      <span class="brand-dot"></span>
      <span class="brand-name">GRANITE RIM</span>
    </div>

    <div class="contact contact--left row-1">
      <span>844-GR-WHEEL</span>
      <svg viewBox="0 0 24 24" aria-hidden="true"><path d="M6.6 10.8c1.4 2.8 3.8 5.1 6.6 6.6l2.2-2.2c.3-.3.7-.4 1-.2 1.1.4 2.3.6 3.6.6.6 0 1 .4 1 1V20c0 .6-.4 1-1 1C10.6 21 3 13.4 3 4c0-.6.4-1 1-1h3.5c.6 0 1 .4 1 1 0 1.3.2 2.5.6 3.6.1.3 0 .7-.2 1z"/></svg>
    </div>
    <div class="contact contact--left row-2">
      <span>561-278-9053</span>
      <svg viewBox="0 0 24 24" aria-hidden="true"><path d="M7 2h8l3 3v5H7zM4 11h16a2 2 0 0 1 2 2v7a2 2 0 0 1-2 2H4a2 2 0 0 1-2-2v-7a2 2 0 0 1 2-2zm3 4v5h10v-5z"/></svg>
    </div>

    <div class="contact contact--right row-1">
      <svg viewBox="0 0 24 24" aria-hidden="true"><path d="M7 1h10a2 2 0 0 1 2 2v18a2 2 0 0 1-2 2H7a2 2 0 0 1-2-2V3a2 2 0 0 1 2-2zm0 3v14h10V4z"/></svg>
      <span>561-390-7714</span>
    </div>
    <div class="contact contact--right row-2">
      <svg viewBox="0 0 24 24" aria-hidden="true"><path d="M2 5h20v14H2zm2 2v.5l8 5 8-5V7zm0 2.8V17h16V9.8l-8 5z"/></svg>
      <span>info@graniterim-example.com</span>
    </div>

    <div class="website">www.graniterimsupply-example.com</div>

    <div class="band">
      <div class="band-company">GRANITE RIM SUPPLY, LLC</div>
      <div class="band-address">5126 Marston Lane West Palm Beach, FL 33411</div>
    </div>
  </div>
</body>
</html>
```